Boutique Store Selling Antiques and Unique Finds

I need a Web Page designed for my Store Called "Willow Lane". I would like a very classic, muted design that looks European when pulled up. I will be selling Antiques from all over the world and Unique finds that have reproduced. I will also be selling high-end purses and jewelry with unique, reasonable products for the every-day buyer as well.

Target Market(s)

25-70 year old men and women;)

Coding

Coded - Design and coding required

Number of Pages Required

1 page

Colors

Designer to choose only greyscale colors for use in the design.

Requirements
Must have
• I want it

```html
<!DOCTYPE html>
<html lang="en">
<head>
<meta charset="utf-8">
<title>Willow Lane — Antiques &amp; Unique Finds</title>
<link href="https://fonts.googleapis.com/css2?family=Cinzel:wght@400;600&family=Jost:wght@300;400;500;600&display=swap" rel="stylesheet">
<style>
:root{
  --ink:#1b1b1b;
  --text:#3a3a3a;
  --muted:#6b6b6b;
  --band:#ecebe9;
  --band-light:#f6f6f5;
  --white:#ffffff;
  --panel:#3d3d3d;
  --accent:#7c7c7c;
  --line:#d6d6d6;
  --ring:#cfcfcf;
  --dark:#1c1c1c;
}
*{box-sizing:border-box;margin:0;padding:0}
html,body{width:1200px;height:3627px;overflow:hidden}
body{position:relative;background:var(--white);font-family:'Jost',sans-serif;color:var(--text)}

/* header */
.site-header{position:absolute;left:0;top:0;width:1200px;height:114px;background:var(--white)}
.top-link{position:absolute;top:18px;font-size:12px;letter-spacing:.5px;color:var(--ink)}
.nav{position:absolute;top:72px;font-size:14px;letter-spacing:.6px;color:var(--text)}
.nav.active{color:var(--ink)}
.nav.active::after{content:"";position:absolute;left:-4px;right:-4px;top:36px;height:2px;background:var(--ink)}
.brand{position:absolute;left:0;width:1200px;top:60px;text-align:center;font-family:'Cinzel',serif;font-size:25px;letter-spacing:4px;color:var(--ink)}
.brand-dot{position:absolute;left:592px;top:28px;width:16px;height:16px;border-radius:50%;background:var(--ink)}

/* hero */
.hero{position:absolute;left:0;top:114px;width:1200px;height:601px;background:linear-gradient(120deg,#3e3e3e 0%,#6a6a6a 35%,#8e8e8e 55%,#555 80%,#2c2c2c 100%)}
.hero-ring{position:absolute;left:99px;top:80px;width:428px;height:428px;border-radius:50%;border:1.5px solid rgba(255,255,255,.8)}
.hero-disc{position:absolute;left:111px;top:90px;width:404px;height:404px;border-radius:50%;background:#141414}
.hero-copy{position:absolute;left:111px;top:230px;width:404px;text-align:center;color:var(--white)}
.hero-kicker{font-size:17px;letter-spacing:2.5px;font-weight:300}
.hero-title{font-family:'Cinzel',serif;font-size:28px;line-height:36px;margin-top:4px}
.hero-btn{display:inline-block;margin-top:22px;width:168px;height:38px;border:1.5px solid var(--white);font-size:12px;letter-spacing:2px;font-weight:500;line-height:36px}
.hero-dots{position:absolute;left:570px;top:569px;display:flex;gap:13px}
.hero-dots span{width:11px;height:11px;border-radius:50%;background:rgba(255,255,255,.5)}
.hero-dots span.on{background:var(--white)}

/* sections */
.band{position:absolute;left:0;width:1200px;background:var(--band)}
.section-title{position:absolute;left:0;width:1200px;text-align:center;font-size:30px;letter-spacing:4px;color:var(--ink);font-weight:300}
.section-title b{font-weight:600}
.title-rule{position:absolute;left:584px;width:32px;height:2px;background:var(--ink)}

/* product categories */
.cat{position:absolute;width:236px;height:236px;border-radius:50%;border:1.5px solid var(--ring);background:var(--band-light)}
.cat-photo{position:absolute;left:8px;top:8px;width:218px;height:218px;border-radius:50%}
.cat-label{position:absolute;width:300px;text-align:center;font-size:16px;letter-spacing:2.5px;font-weight:600;color:var(--ink)}

/* about */
.about-photo{position:absolute;left:107px;top:1271px;width:728px;height:444px;background:linear-gradient(180deg,#8a8a8a 0%,#c4c4c4 40%,#555 70%,#d4d4d4 100%)}
.about-frame{position:absolute;left:121px;top:1285px;width:700px;height:416px;border:2px solid rgba(255,255,255,.85)}
.about-card{position:absolute;left:680px;top:1340px;width:408px;height:295px;background:var(--panel);color:var(--white);text-align:center}
.about-inner{position:absolute;left:10px;top:10px;right:10px;bottom:10px;border:1px solid rgba(255,255,255,.6)}
.about-mark{position:absolute;left:196px;top:42px;width:14px;height:14px;border-radius:50%;background:var(--white)}
.about-kicker{position:absolute;left:0;right:0;top:68px;font-family:'Cinzel',serif;font-size:13px;letter-spacing:1.5px}
.about-title{position:absolute;left:0;right:0;top:88px;font-size:27px;letter-spacing:3px;font-weight:300}
.about-title b{font-weight:600}
.about-body{position:absolute;left:30px;right:30px;top:136px;font-family:Arial,sans-serif;font-size:11px;line-height:19px}
.about-btn{position:absolute;left:138px;top:204px;width:120px;height:33px;background:var(--accent);font-size:11px;letter-spacing:1.5px;font-weight:600;line-height:33px}

/* shop cards */
.shop-card{position:absolute;top:1853px;width:326px;height:298px;border:1px solid var(--line);background:var(--white);text-align:center}
.shop-photo{width:100%;height:221px}
.shop-name{margin-top:18px;font-size:15px;letter-spacing:1px;color:var(--ink)}
.shop-price{margin-top:4px;font-size:14px;font-weight:500;color:var(--ink)}
.pager{position:absolute;top:2206px;left:580px;display:flex;gap:11px}
.pager span{width:7px;height:7px;border-radius:50%;background:#c9c9c9}
.pager span.on{background:var(--ink)}

/* popular */
.pop-card{position:absolute;top:2412px;width:497px;height:398px}
.pop-photo{position:absolute;left:0;top:0;width:100%;height:300px}
.pop-label{position:absolute;left:17px;right:17px;top:305px;height:82px;background:var(--band-light);border:1px solid #c8c8c8;text-align:center}
.pop-label-inner{position:absolute;left:4px;top:4px;right:4px;bottom:4px;border:1px solid #b0b0b0}
.pop-name{position:relative;margin-top:22px;font-size:17px;letter-spacing:1px;color:var(--ink)}
.pop-price{position:relative;margin-top:8px;font-size:14px;font-weight:500;color:var(--ink)}

/* newsletter */
.newsletter{position:absolute;left:0;top:2909px;width:1200px;height:380px;background:linear-gradient(90deg,#222 0%,#3e3e3e 30%,#252525 60%,#333 100%)}
.news-title{position:absolute;left:0;width:1200px;top:94px;text-align:center;color:var(--white);font-size:27px;letter-spacing:3.5px;font-weight:600}
.news-sub{position:absolute;left:0;width:1200px;top:126px;text-align:center;color:var(--white);font-size:27px;letter-spacing:3.5px;font-weight:300}
.news-rule{position:absolute;left:584px;top:168px;width:32px;height:2px;background:var(--white)}
.news-input{position:absolute;left:310px;top:197px;width:397px;height:42px;background:var(--white);font-family:Arial,sans-serif;font-size:11px;color:#555;line-height:42px;padding-left:18px}
.news-btn{position:absolute;left:715px;top:197px;width:162px;height:42px;background:var(--accent);color:var(--white);text-align:center;font-size:13px;letter-spacing:2px;font-weight:600;line-height:42px}

/* footer */
.foot-head{position:absolute;top:3356px;font-size:13px;font-weight:600;letter-spacing:.5px;color:var(--ink)}
.foot-list{position:absolute;top:3384px;list-style:none;font-size:10px;line-height:25.5px;color:var(--text)}
.foot-list li{display:flex;align-items:center}
.foot-list .dot{width:10px;height:10px;border-radius:50%;border:1.3px solid var(--ink);margin-right:14px}
.foot-divider{position:absolute;top:3345px;width:1px;height:147px;background:var(--line)}
.foot-rule{position:absolute;left:0;top:3558px;width:1200px;height:1px;background:var(--line)}
.foot-small{position:absolute;top:3584px;font-size:10px;color:var(--text)}
.foot-brand{position:absolute;left:0;width:1200px;top:3578px;text-align:center;font-family:'Cinzel',serif;font-size:16px;letter-spacing:2px;color:var(--ink)}
</style>
</head>
<body>

<header class="site-header">
  <span class="top-link" style="left:98px">MY ACCOUNT</span>
  <span class="top-link" style="left:1033px;top:22px">BASKET (0)</span>
  <span class="nav active" style="left:95px">HOME</span>
  <span class="nav" style="left:184px">SHOP ONLINE</span>
  <span class="nav" style="left:322px">PRODUCTS</span>
  <span class="nav" style="left:802px">DISCOVER</span>
  <span class="nav" style="left:914px">BLOGS</span>
  <span class="nav" style="left:1006px">CONTACT US</span>
  <span class="brand-dot"></span>
  <div class="brand">WILLOW LANE</div>
</header>

<section class="hero" role="img" aria-label="Tufted antique sofa in a wood-panelled library with a patterned rug">
  <div class="hero-ring"></div>
  <div class="hero-disc"></div>
  <div class="hero-copy">
    <div class="hero-kicker">SHOP NOW</div>
    <div class="hero-title">ANTIQUES FROM<br>ALL OVER THE WORLD</div>
    <div class="hero-btn">VIEW PRODUCTS</div>
  </div>
  <div class="hero-dots"><span class="on"></span><span></span><span></span></div>
</section>

<section class="band" style="top:715px;height:485px">
  <h2 class="section-title" style="top:52px">OUR <b>PRODUCTS</b></h2>
  <div class="title-rule" style="top:92px"></div>

  <div class="cat" style="left:83px;top:131px"><div class="cat-photo" role="img" aria-label="Gilded antique cabinet and clock" style="background:radial-gradient(circle,#bdbdbd,#4e4e4e)"></div></div>
  <div class="cat" style="left:347px;top:131px"><div class="cat-photo" role="img" aria-label="Brass gramophone showpiece" style="background:radial-gradient(circle,#a8a8a8,#2a2a2a)"></div></div>
  <div class="cat" style="left:610px;top:131px"><div class="cat-photo" role="img" aria-label="Metal vase and small antique objects" style="background:radial-gradient(circle,#8a8a8a,#3c3c3c)"></div></div>
  <div class="cat" style="left:875px;top:131px"><div class="cat-photo" role="img" aria-label="Ornate bronze mantel clock" style="background:radial-gradient(circle,#a0a0a0,#454545)"></div></div>

  <div class="cat-label" style="left:51px;top:387px">ANTIQUES</div>
  <div class="cat-label" style="left:320px;top:387px">SHOWPIECE</div>
  <div class="cat-label" style="left:580px;top:387px">PURSES</div>
  <div class="cat-label" style="left:845px;top:387px">CLOCK</div>
</section>

<section class="about">
  <div class="about-photo" role="img" aria-label="Carved wooden antique sofa beneath framed paintings"></div>
  <div class="about-frame"></div>
  <div class="about-card">
    <div class="about-inner"></div>
    <span class="about-mark"></span>
    <div class="about-kicker">ABOUT US</div>
    <div class="about-title"><b>WILLOW</b> LANE</div>
    <p class="about-body">Lorem Ipsum is simply dummy text of the printing and typesetting industry. Lorem Ipsum has been the industry's standard dummy text ever since the 1500s, when an unknown printer.</p>
    <div class="about-btn">LEARN MORE</div>
  </div>
</section>

<section class="shop">
  <h2 class="section-title" style="top:1772px">SHOP <b>ONLINE</b></h2>
  <div class="title-rule" style="top:1818px"></div>

  <article class="shop-card" style="left:94px">
    <div class="shop-photo" role="img" aria-label="Leather and brocade antique sofa" style="background:linear-gradient(180deg,#2e2e2e,#6e6e6e 55%,#c6c6c6)"></div>
    <div class="shop-name">PRODUCT ANTIQUE CHAIR</div>
    <div class="shop-price">$1,350.00</div>
  </article>
  <article class="shop-card" style="left:439px">
    <div class="shop-photo" role="img" aria-label="Antique pistol and gold coins on wood" style="background:linear-gradient(135deg,#555,#8e8e8e 50%,#3a3a3a)"></div>
    <div class="shop-name">PRODUCT ANTIQUE CHAIR</div>
    <div class="shop-price">$1,350.00</div>
  </article>
  <article class="shop-card" style="left:786px">
    <div class="shop-photo" role="img" aria-label="Painted brass figurines" style="background:linear-gradient(135deg,#6a6a6a,#9a9a9a 45%,#444 75%,#a8a8a8)"></div>
    <div class="shop-name">PRODUCT ANTIQUE CHAIR</div>
    <div class="shop-price">$1,350.00</div>
  </article>

  <div class="pager"><span class="on"></span><span></span><span></span></div>
</section>

<section class="band" style="top:2271px;height:638px">
  <h2 class="section-title" style="top:59px"><b>POPULAR</b> ITEMS</h2>
  <div class="title-rule" style="top:105px"></div>
</section>

<article class="pop-card" style="left:94px;background:#111">
  <div class="pop-photo" role="img" aria-label="Diamond necklace on driftwood" style="background:linear-gradient(135deg,#252525,#6a6a6a 50%,#1c1c1c)"></div>
  <div class="pop-label"><div class="pop-label-inner"></div><div class="pop-name">JEWELERY ITEMS</div><div class="pop-price">$1,150.00</div></div>
</article>
<article class="pop-card" style="left:610px;background:#bdbdbd">
  <div class="pop-photo" role="img" aria-label="Designer handbag on a display shelf" style="background:linear-gradient(90deg,#dedede,#8f8f8f 50%,#d6d6d6)"></div>
  <div class="pop-label"><div class="pop-label-inner"></div><div class="pop-name">HIGH END PURSES</div><div class="pop-price">$750.00</div></div>
</article>

<section class="newsletter" role="img" aria-label="Pocket watch and cigar on a dark wooden table">
  <div class="news-title">SIGN UP TO OUR NEWSLETTER</div>
  <div class="news-sub">TO STAY UP TO DATE</div>
  <div class="news-rule"></div>
  <div class="news-input">Your Email address</div>
  <div class="news-btn">SUBSCRIBE</div>
</section>

<footer>
  <div class="foot-head" style="left:158px">ABOUT US</div>
  <ul class="foot-list" style="left:158px"><li>A Family Business</li><li>Philosophy and Ethos</li><li>Charity and Community</li><li>Press</li><li>Careers</li></ul>
  <div class="foot-divider" style="left:359px"></div>

  <div class="foot-head" style="left:428px">SPECIAL PRODUCTS</div>
  <ul class="foot-list" style="left:428px"><li>Purse</li><li>Furniture</li><li>Jewellery Items</li><li>View All</li></ul>
  <div class="foot-divider" style="left:656px"></div>

  <div class="foot-head" style="left:736px">RESOURCES</div>
  <ul class="foot-list" style="left:736px"><li>Terms and Conditions</li><li>Privacy Policy</li><li>Contact</li></ul>
  <div class="foot-divider" style="left:915px"></div>

  <div class="foot-head" style="left:983px">SOCIAL</div>
  <ul class="foot-list" style="left:983px"><li><span class="dot"></span>Snapfolio</li><li><span class="dot"></span>Friendwall</li><li><span class="dot"></span>Pinboard</li><li><span class="dot"></span>Chirper</li></ul>

  <div class="foot-rule"></div>
  <div class="foot-small" style="left:155px;top:3580px">2021 © Willow Lane &nbsp;|&nbsp; All Right Reserved</div>
  <div class="foot-brand">WILLOW LANE</div>
  <div class="foot-small" style="left:887px">Cookies</div>
  <div class="foot-small" style="left:942px">Sitemap</div>
  <div class="foot-small" style="left:998px">Terms of Use</div>
</footer>

</body>
</html>
```